IT Support Business needs a Flyer Designed

Have just had new logo and business cards made for new business called Byte Harbor, am now in need of a new flyer design. Byte Harbor will be providing home and small business it support.
Updates
Byte Harbor flyer design brief has been uploaded. The contest has also been changed to payment guaranteed.
If you need anymore information please feel free to contact myself.
Project Deadline Extended
Reason: I signed up early to take advantage of the artfolly 24 hour sale, and was a few days late in providing a design brief. Therefore I am extending the deadline by 2 days, to ensure it lasts for a good 2 weeks.
Have worked on and refined the Design Brief a bit more, hoping it makes it a bit clearer as to what I want on the flyer. If you have any questions please do not hesitate to ask.
I have refined the design brief overnight, after receiving some feedback, please refer to newly uploaded file for this morning. I am hoping it makes things clearer and easier.
Industry/Entity Type
Small Business

```html
<!DOCTYPE html>
<html lang="en">
<head>
<meta charset="UTF-8">
<title>Byte Harbor – Computer Repair Flyer</title>
<link href="https://fonts.googleapis.com/css2?family=Bitter:wght@400&family=PT+Sans:wght@400;700&display=swap" rel="stylesheet">
<style>
  :root {
    --brand-blue: #1e679f;
    --deep-blue: #17578a;
    --accent-red: #e2392c;
    --paper: #ffffff;
    --page: #eef0f2;
  }
  html, body {
    margin: 0;
    padding: 0;
    width: 1200px;
    height: 798px;
    overflow: hidden;
    background: var(--page);
  }
  .flyer {
    position: relative;
    width: 1200px;
    height: 798px;
    overflow: hidden;
    font-family: "PT Sans", Arial, sans-serif;
  }
  .flyer-backdrop {
    position: absolute;
    inset: 0;
  }
  .service {
    position: absolute;
    width: 170px;
    margin-left: -85px;
    text-align: center;
    color: var(--paper);
    font-size: 17px;
    line-height: 19px;
  }
  .service svg {
    display: block;
    margin: 0 auto 14px;
    width: 64px;
    height: 64px;
  }
  .brand {
    position: absolute;
    right: 30px;
    top: 58px;
    display: flex;
    align-items: center;
    gap: 14px;
    font-family: "PT Sans", Arial, sans-serif;
    font-weight: 700;
    font-size: 46px;
    letter-spacing: 1px;
    color: var(--brand-blue);
    text-transform: uppercase;
  }
  .brand-dot {
    width: 26px;
    height: 26px;
    border-radius: 50%;
    background: var(--accent-red);
  }
  .headline {
    position: absolute;
    right: 30px;
    top: 176px;
    margin: 0;
    text-align: right;
    font-family: "Bitter", Georgia, serif;
    font-weight: 400;
    font-size: 58px;
    line-height: 71px;
    color: var(--accent-red);
  }
  .offers {
    position: absolute;
    right: 30px;
    top: 540px;
    margin: 0;
    padding: 0;
    list-style: none;
    text-align: right;
    color: var(--accent-red);
    font-size: 23px;
    line-height: 34px;
  }
  .offers li { margin-bottom: 10px; }
  .pointer {
    display: inline-block;
    width: 14px;
    height: 20px;
    margin-right: 8px;
    vertical-align: -2px;
  }
</style>
</head>
<body>
<main class="flyer">
  <svg class="flyer-backdrop" viewBox="0 0 1200 798" width="1200" height="798">
    <rect width="1200" height="798" fill="var(--brand-blue)"/>
    <path d="M659 0 L1200 0 L1200 798 L690 798 C555 620 555 180 659 0 Z" fill="var(--paper)"/>
    <circle cx="595" cy="393" r="256" fill="var(--paper)"/>
    <path d="M718 180 A246 246 0 0 1 718 606" fill="none" stroke="var(--brand-blue)" stroke-width="3"/>
    <defs>
      <radialGradient id="photoTone" cx="0.55" cy="0.45" r="0.6">
        <stop offset="0" stop-color="#e9eef3"/>
        <stop offset="0.6" stop-color="#b9c8d6"/>
        <stop offset="1" stop-color="#8fa6ba"/>
      </radialGradient>
    </defs>
    <circle class="hero-photo" cx="595" cy="393" r="238" fill="url(#photoTone)" role="img" aria-label="Photo of hands typing on a laptop keyboard with digital interface graphics"/>
  </svg>

  <!-- Services row 1 -->
  <div class="service" style="left:105px; top:44px;">
    <svg viewBox="0 0 64 64" fill="none" stroke="#fff" stroke-width="3">
      <rect x="6" y="10" width="48" height="34" rx="2"/>
      <path d="M22 54h16M30 44v10"/>
      <path d="M24 36l14-14m2-6a6 6 0 1 0 4 4" stroke-linecap="round"/>
    </svg>
    Computer<br>Repair, Service,<br>Install And<br>Upgrade
  </div>
  <div class="service" style="left:257px; top:44px;">
    <svg viewBox="0 0 64 64" fill="#fff" stroke="#fff" stroke-width="3">
      <rect x="20" y="4" width="24" height="16" rx="2"/>
      <path d="M32 20v10M10 30h44M10 30v10M32 30v10M54 30v10" fill="none"/>
      <circle cx="10" cy="48" r="8"/><circle cx="32" cy="48" r="8"/><circle cx="54" cy="48" r="8"/>
    </svg>
    Setting Up<br>Secure<br>Networks
  </div>
  <div class="service" style="left:403px; top:44px;">
    <svg viewBox="0 0 64 64" fill="none" stroke="#fff" stroke-width="3">
      <rect x="6" y="6" width="52" height="44" rx="4"/>
      <path d="M30 56V28a4 4 0 0 1 8 0v12l10 2v14" stroke-linejoin="round"/>
    </svg>
    Setting up<br>New<br>Hardware
  </div>

  <!-- Services row 2 -->
  <div class="service" style="left:105px; top:328px;">
    <svg viewBox="0 0 64 64" fill="#fff" stroke="#fff" stroke-width="2">
      <rect x="2" y="8" width="8" height="8"/><rect x="12" y="8" width="8" height="8"/><rect x="22" y="8" width="8" height="8"/>
      <rect x="32" y="8" width="8" height="8"/><rect x="42" y="8" width="8" height="8" fill="none"/><rect x="52" y="8" width="8" height="8" fill="none"/>
      <path d="M34 24v30l8-8 6 12 4-2-6-12h10z"/>
    </svg>
    Software<br>Install And<br>Configuration
  </div>
  <div class="service" style="left:257px; top:328px;">
    <svg viewBox="0 0 64 64" fill="#fff" stroke="#fff" stroke-width="3" stroke-linecap="round">
      <path d="M32 14a14 14 0 0 0-8 25v7h16v-7a14 14 0 0 0-8-25z"/>
      <path d="M26 52h12M28 58h8M32 2v6M12 10l4 4M52 10l-4 4M4 28h6M54 28h6" fill="none"/>
    </svg>
    Software<br>Tricks, Tips<br>and Tutorials
  </div>

  <!-- Services row 3 -->
  <div class="service" style="left:105px; top:624px;">
    <svg viewBox="0 0 64 64" fill="none" stroke="#fff" stroke-width="3">
      <rect x="4" y="6" width="40" height="28" fill="#fff"/>
      <path d="M4 6l20 16 20-16" stroke="var(--brand-blue)"/>
      <circle cx="44" cy="44" r="14"/><circle cx="44" cy="44" r="5"/><path d="M49 40v8a4 4 0 0 0 8 0"/>
    </svg>
    Internet<br>and Email<br>Setup
  </div>
  <div class="service" style="left:257px; top:624px;">
    <svg viewBox="0 0 64 64" fill="none" stroke="#fff" stroke-width="3" stroke-linejoin="round">
      <path d="M16 46a12 12 0 0 1 0-24 16 16 0 0 1 30-4 12 12 0 0 1 4 24"/>
      <path d="M22 34h14v-6l10 10-10 10v-6H22z" fill="#fff"/>
      <path d="M40 54H28v6l-10-10 10-10" fill="#fff" stroke="none"/>
    </svg>
    Data Backup<br>and Recovery
  </div>
  <div class="service" style="left:403px; top:624px;">
    <svg viewBox="0 0 64 64" fill="none" stroke="#fff" stroke-width="4" stroke-linecap="round">
      <path d="M12 36V28a20 20 0 0 1 40 0v8"/>
      <rect x="6" y="30" width="10" height="16" rx="3" fill="#fff"/>
      <rect x="48" y="30" width="10" height="16" rx="3" fill="#fff"/>
      <path d="M53 46c0 8-8 12-16 12"/>
    </svg>
    Onsite and<br>Remote<br>Support<br>Available
  </div>

  <div class="brand"><span class="brand-dot"></span>Byte Harbor</div>

  <h1 class="headline">Computer<br>Repair<br>You Can<br>Depend On</h1>

  <ul class="offers">
    <li><svg class="pointer" viewBox="0 0 14 20"><path d="M0 0v16l4-4 3 7 3-1-3-7h6z" fill="var(--brand-blue)"/></svg>$40 Per Hour Specific Job,<br>Or Am Happy To Bundle, Provide<br>Flexible Pricing For More Complex Tasks</li>
    <li><svg class="pointer" viewBox="0 0 14 20"><path d="M0 0v16l4-4 3 7 3-1-3-7h6z" fill="var(--brand-blue)"/></svg>No Call Out Fee</li>
    <li><svg class="pointer" viewBox="0 0 14 20"><path d="M0 0v16l4-4 3 7 3-1-3-7h6z" fill="var(--brand-blue)"/></svg>Friendly, Hassle Free, Independent<br>Advice And Recommendations Given</li>
  </ul>
</main>
</body>
</html>
```